Restyle corporate identity (+ logo) for a road construction company

We need a new logo and stationary design for our company VARNOK path. VARNOK path® increases the road base strength, while reducing major costs and time of road construction. Attached some examples of the current design.

Our wishes for the new logo:
- Business look
- Style sheet
- Modern

More information: www.varnokpath.example
Updates

Target Market(s)

Government

Industry/Entity Type

Construction

Requirements
Must have
• Logo (with road sign) + text

```html
<!DOCTYPE html>
<html lang="en">
<head>
<meta charset="UTF-8">
<title>VARNOK path — business cards</title>
<link rel="stylesheet" href="https://fonts.googleapis.com/css2?family=Open+Sans:wght@400;600&display=swap">
<style>
  :root {
    --backdrop: #8b8c8e;
    --card-white: #ececee;
    --brand-blue: #1a7fe0;
    --brand-blue-deep: #1476da;
    --text-grey: #4a4a4c;
    --muted-grey: #8a8a8c;
    --white: #ffffff;
    --white-soft: rgba(255,255,255,0.9);
  }
  * { margin: 0; padding: 0; box-sizing: border-box; }
  html, body {
    width: 1105px; height: 1200px; overflow: hidden;
    background: var(--backdrop);
    font-family: "Open Sans", Arial, sans-serif;
  }
  .card {
    position: absolute; left: 182px; width: 746px; height: 425px;
  }
  .card-front { top: 119px; background: var(--card-white); }
  .card-back { top: 637px; background: var(--brand-blue-deep); }

  .front-logo {
    position: absolute; left: 233px; top: 177px;
    display: flex; align-items: center; gap: 18px;
  }
  .card .front-logo { left: 51px; top: 58px; }
  .logo-square {
    width: 80px; height: 80px; border-radius: 10px;
    background: var(--brand-blue);
  }
  .logo-name {
    color: var(--brand-blue); font-weight: 600;
    font-size: 40px; line-height: 44px; letter-spacing: 2px;
  }

  .address {
    position: absolute; left: 52px; top: 209px;
    color: var(--text-grey); font-size: 19px; line-height: 26px;
  }
  .contact-list {
    position: absolute; left: 52px; top: 299px; list-style: none;
    color: var(--text-grey); font-size: 19px; line-height: 29px;
  }
  .contact-list li { display: flex; align-items: center; gap: 10px; }
  .contact-list svg { width: 17px; height: 17px; fill: var(--brand-blue); }

  .person {
    position: absolute; right: 48px; top: 265px; text-align: right;
  }
  .person-name {
    color: var(--brand-blue); font-weight: 600; font-size: 25px; line-height: 32px;
  }
  .person-role { color: var(--muted-grey); font-size: 19px; line-height: 26px; }
  .accent-bar {
    position: absolute; right: 0; top: 271px; width: 17px; height: 53px;
    background: var(--brand-blue);
  }

  .back-brand {
    position: absolute; right: 56px; top: 225px; text-align: right;
    color: var(--white); font-weight: 600;
    font-size: 56px; line-height: 64px; letter-spacing: 4px;
  }
  .back-url {
    position: absolute; right: 56px; top: 361px;
    color: var(--white-soft); font-size: 20px; letter-spacing: 1px;
  }
</style>
</head>
<body>
  <section class="card card-front">
    <div class="front-logo">
      <div class="logo-square"></div>
      <div class="logo-name">VARNOK<br>PATH</div>
    </div>
    <p class="address">Lindqvist Kade 58<br>3012 TX Veldhaven<br>The Netherlands</p>
    <ul class="contact-list">
      <li><svg viewBox="0 0 24 24"><path d="M6.6 10.8a15.1 15.1 0 0 0 6.6 6.6l2.2-2.2c.3-.3.7-.4 1-.2 1.1.4 2.3.6 3.6.6.6 0 1 .4 1 1V20c0 .6-.4 1-1 1A17 17 0 0 1 3 4c0-.6.4-1 1-1h3.5c.6 0 1 .4 1 1 0 1.3.2 2.5.6 3.6.1.3 0 .7-.2 1z"/></svg>555 210 4873</li>
      <li><svg viewBox="0 0 24 24"><path d="M2 5h20v14H2z M2 5l10 8 10-8" stroke="#ececee" stroke-width="1.5"/></svg>info@varnokpath.example</li>
      <li><svg viewBox="0 0 24 24"><circle cx="12" cy="12" r="10"/><path d="M2 12h20M12 2c3 3 3 17 0 20M12 2c-3 3-3 17 0 20" stroke="#ececee" stroke-width="1.5" fill="none"/></svg>www.varnokpath.example</li>
    </ul>
    <div class="person">
      <div class="person-name">MAREN TOLVIK</div>
      <div class="person-role">CEO/Founder</div>
    </div>
    <div class="accent-bar"></div>
  </section>

  <section class="card card-back">
    <div class="back-brand">VARNOK<br>PATH</div>
    <div class="back-url">www.varnokpath.example</div>
  </section>
</body>
</html>
```